Website for a Psychologist in Private Practice

I need a cool web design for my website: www.drkalvoric.com. I would like it to look professional. Keep all the current content and add: Space for video; radio spots (see Silver Cedar Tunes Logo below for those); Quick Inquiry; Friendora link; 5 star rating on Rivo; a map; reviews from former patients. I am open to suggestions.

Target Market(s)

Those seeking individual and marital counseling.

Industry/Entity Type

Mental Health

Number of Pages Required

1 page

Font styles to use
Sans Serif
Other font styles liked:
• I'm open but no hard to read script

Requirements
Must have
• All the content on my home page with link for video and radio spots. List services and degrees and expertices (pics not necessary).
Nice to have
• A video of me and radio conversations (logo of Silver Cedar Tunes radio attached).
Should not have
• Cartoons, comedy, etc.... I don't need pictures of services (marital, depression, etc...) Just list those.

```html
<!DOCTYPE html>
<html lang="en">
<head>
<meta charset="utf-8">
<title>Dr. Marla J. Kalvoric – Clinical Psychologist</title>
<link href="https://fonts.googleapis.com/css2?family=Josefin+Sans:wght@400;600;700&family=Roboto:wght@400;500;700&family=Roboto+Condensed:wght@400;700&family=Lobster&display=swap" rel="stylesheet">
<style>
:root{
  --gold:#c8b04e;
  --navy:#1f5a82;
  --blue-btn:#7ea4cc;
  --pill:#2e86c8;
  --ink:#2a2a2a;
  --body:#4a4540;
  --white:#ffffff;
  --field:#ececec;
  --badge-red:#d9dde6;
  --badge-green:#dfe4cf;
}
*{box-sizing:border-box;margin:0;padding:0}
html,body{width:1200px;height:2765px;overflow:hidden}
body{position:relative;font-family:"Roboto",Arial,sans-serif;color:var(--body);
  background:linear-gradient(180deg,#7db8c4 720px,#a9c9c4 860px,#d0c7b4 1080px,#d8cebf 1400px,#cdc3b3 2400px)}
.abs{position:absolute}

/* hero */
.hero-photo{left:0;top:0;width:1200px;height:720px;
  background:linear-gradient(160deg,#6f9fbf 0%,#b7b3a6 55%,#e3d6c0 100%)}
.portrait-photo{left:720px;top:0;width:480px;height:720px;
  background:linear-gradient(90deg,rgba(214,186,150,0) 0%,rgba(214,186,150,.85) 40%,#c9a07e 72%,#4a6c94 100%)}
.portrait-name{left:800px;top:596px;font-family:"Josefin Sans",sans-serif;font-weight:600;font-size:22px;color:var(--white)}
.topbar{left:0;top:33px;width:1200px;height:100px;background:rgba(200,176,78,.94)}
.brand{left:74px;top:58px;font-family:"Josefin Sans",sans-serif;font-size:34px;color:var(--white);font-weight:400}
.brand b{font-weight:600}
.contact-strip{right:62px;top:51px;display:flex;gap:36px;font-size:14px;color:var(--white);align-items:center}
.contact-strip span{display:flex;align-items:center;gap:8px}
.main-nav{right:62px;top:92px;display:flex;gap:22px;font-family:"Roboto Condensed",sans-serif;font-weight:700;font-size:16px;color:var(--white)}
.expertise{left:133px;top:345px;width:507px;height:180px;background:rgba(40,50,60,.5);border-radius:6px;color:var(--white);text-align:center;padding-top:24px;font-family:"Josefin Sans",sans-serif}
.expertise h2{font-weight:400;font-size:23px;line-height:28px;letter-spacing:.5px}
.expertise p{font-size:15px;line-height:20px;margin-top:6px}
.expertise h3{font-weight:400;font-size:20px;line-height:24px;margin-top:5px}
.expertise p.last{margin-top:7px}
.slide-arrow{top:416px;width:34px;height:34px;border:2px solid rgba(255,255,255,.8);border-radius:50%;background:rgba(255,255,255,.25)}

/* media */
.radio-card{left:74px;top:750px;width:424px;height:247px;background:rgba(255,255,255,.55);border-radius:8px}
.radio-photo{left:30px;top:38px;width:110px;height:90px;border-radius:8px;background:linear-gradient(180deg,#8a5a34,#5b3a22)}
.radio-title{left:160px;top:56px;font-family:"Lobster",cursive;font-size:44px;color:#3a2a1c}
.radio-show{left:62px;top:160px;display:flex;align-items:center;gap:10px;font-family:"Roboto",sans-serif;font-weight:700;font-size:26px;color:#d4205c}
.radio-show i{width:16px;height:16px;background:#d4205c;display:block}
.radio-guests{left:88px;top:196px;font-family:"Roboto",sans-serif;font-size:16px;color:#6a4a3a}
.video-frame{left:525px;top:654px;width:600px;height:347px;background:var(--white);padding:10px;box-shadow:0 2px 10px rgba(0,0,0,.25)}
.video-still{width:100%;height:100%;background:linear-gradient(180deg,#1a3a52 0%,#1f6f80 55%,#14495a 100%);position:relative}
.video-bar{position:absolute;left:0;bottom:0;width:100%;height:30px;background:rgba(0,0,0,.6);color:#fff;font-size:10px;display:flex;align-items:center;padding:0 12px;gap:14px}
.video-progress{position:absolute;left:0;bottom:30px;width:100%;height:3px;background:rgba(255,255,255,.3)}
.video-progress i{display:block;width:14%;height:100%;background:#e0463a}

/* welcome */
.welcome{left:76px;top:1056px;width:670px}
.welcome .kicker{font-family:"Josefin Sans",sans-serif;font-size:27px;color:var(--ink)}
.welcome h1{font-family:"Josefin Sans",sans-serif;font-size:34px;font-weight:400;color:var(--ink);margin-top:-4px}
.welcome h1 b{font-weight:600}
.welcome p{font-size:13.6px;line-height:24px;margin-top:14px}
.welcome p:first-of-type{margin-top:6px}

/* inquiry */
.inquiry{left:794px;top:1061px;width:328px;height:502px;background:var(--white);border-radius:6px;box-shadow:0 1px 6px rgba(0,0,0,.2);overflow:hidden}
.inquiry-head{height:128px;background:var(--gold);text-align:center;color:var(--white);padding-top:10px;clip-path:polygon(0 0,100% 0,100% 88%,50% 100%,0 88%)}
.inquiry-head .over{font-family:"Roboto Condensed",sans-serif;font-weight:700;font-size:18px}
.inquiry-head .pill{margin:6px auto 0;width:294px;height:34px;border-radius:17px;background:var(--pill);font-family:"Josefin Sans",sans-serif;font-size:27px;line-height:38px}
.inquiry-head .note{font-size:13px;margin-top:6px;line-height:17px}
.inquiry-form{padding:14px 16px 0}
.field{height:40px;background:var(--field);border-radius:4px;margin-bottom:9px;font-size:13px;color:#666;padding:12px 12px}
.field.tall{height:128px}
.submit{height:40px;background:var(--blue-btn);border-radius:4px;color:#fff;text-align:center;font-weight:700;font-size:15px;line-height:40px;margin-top:12px;border-bottom:3px solid #5a82ad}

/* reviews */
.section-title{left:0;width:1200px;text-align:center;font-family:"Josefin Sans",sans-serif;font-weight:400;font-size:29px;color:var(--ink)}
.title-rule{left:556px;top:1668px;width:88px;height:1px;background:#9a9080}
.reviews{left:42px;top:1718px;width:1116px;display:flex}
.review{flex:1;text-align:center;padding:0 22px;border-left:1px solid rgba(140,130,115,.4);height:340px}
.review:first-child{border-left:none}
.avatar{width:78px;height:78px;border-radius:50%;margin:0 auto;background:linear-gradient(180deg,#8a7a6a,#c9a688);border:3px solid #fff}
.review p{font-size:13.4px;line-height:18.4px;color:#4a4a4a;margin-top:32px}
.review .who{font-family:"Josefin Sans",sans-serif;font-size:18px;margin-top:22px;color:#3a3a3a}
.review .role{font-size:11px;color:#555}

/* giving */
.partners{left:337px;top:2180px;display:flex;gap:11px}
.partner{width:241px;height:105px;background:var(--white);display:flex;align-items:center;justify-content:center}
.partner-mark{width:190px;height:56px;border-radius:6px}
.partner-mark.one{background:var(--badge-red)}
.partner-mark.two{background:var(--badge-green)}

/* footer */
.footer-wave{left:0;top:2330px;width:1200px;height:90px}
.footer{left:0;top:2400px;width:1200px;height:313px;background:var(--navy);color:var(--white)}
.foot-col{position:absolute;top:79px;font-size:13.6px;line-height:24px}
.foot-col h4{font-family:"Roboto Condensed",sans-serif;font-weight:700;font-size:14.5px;line-height:18px}
.foot-col .sub{font-size:13px;line-height:16px;margin-bottom:12px}
.contact-line{display:flex;align-items:flex-start;gap:14px;margin-top:16px}
.map-tile{width:244px;height:161px;background:linear-gradient(135deg,#ece8df,#d9d5cb);margin-top:24px}
.bottom-bar{left:0;top:2713px;width:1200px;height:52px;background:var(--gold);color:var(--white);font-size:13.5px}
.copyright{position:absolute;left:58px;top:17px}
.socials{position:absolute;right:58px;top:15px;display:flex;gap:30px;font-size:15px}
.socials span{display:flex;align-items:center;gap:8px}
.socials i{width:14px;height:14px;border-radius:50%;background:var(--white);display:block}
</style>
</head>
<body>

<div class="abs hero-photo" role="img" aria-label="Photograph of a tropical beach with palm trees at sunset"></div>
<div class="abs portrait-photo" role="img" aria-label="Portrait photograph of the psychologist"></div>
<div class="abs portrait-name">Dr. Marla K</div>

<header>
  <div class="abs topbar"></div>
  <div class="abs brand">Dr. <b>Marla J. Kalvoric</b></div>
  <div class="abs contact-strip">
    <span><svg width="14" height="14" viewBox="0 0 24 24"><path d="M6.6 10.8a15 15 0 0 0 6.6 6.6l2.2-2.2a1 1 0 0 1 1-.25 11.4 11.4 0 0 0 3.6.57 1 1 0 0 1 1 1V20a1 1 0 0 1-1 1A17 17 0 0 1 3 4a1 1 0 0 1 1-1h3.5a1 1 0 0 1 1 1c0 1.25.2 2.45.57 3.57a1 1 0 0 1-.25 1z" fill="#fff"/></svg>Call Now: (555) 318 4402</span>
    <span><svg width="15" height="12" viewBox="0 0 24 18"><rect x="1" y="1" width="22" height="16" fill="none" stroke="#fff" stroke-width="2"/><path d="M1 1l11 9 11-9" fill="none" stroke="#fff" stroke-width="2"/></svg>Email: mk@drkalvoric.com</span>
  </div>
  <nav class="abs main-nav"><span>HOME</span><span>SESSIONS</span><span>RESOURCES</span><span>BIO</span><span>CONTACT</span></nav>
</header>

<div class="abs expertise">
  <h2>〰 EXPERTISE</h2>
  <p>Dating &nbsp;•&nbsp; Marriage &nbsp;•&nbsp; Parenting &amp; Professional</p>
  <h3>RELATIONSHIPS</h3>
  <p class="last">Depression &amp; Anxiety Issues &nbsp;•&nbsp; Personality Disorders &nbsp;•&nbsp; Life Management</p>
</div>
<div class="abs slide-arrow" style="left:25px"><svg width="30" height="30" viewBox="0 0 30 30"><path d="M17 9l-6 6 6 6" fill="none" stroke="#fff" stroke-width="2.5"/></svg></div>
<div class="abs slide-arrow" style="left:1140px"><svg width="30" height="30" viewBox="0 0 30 30"><path d="M13 9l6 6-6 6" fill="none" stroke="#fff" stroke-width="2.5"/></svg></div>

<section class="abs radio-card">
  <div class="abs radio-photo" role="img" aria-label="Photograph of a vintage wooden radio"></div>
  <div class="abs radio-title">Radio Spots</div>
  <div class="abs radio-show"><i></i>Silver Cedar Tunes</div>
  <div class="abs radio-guests">With Mia and Tess</div>
</section>

<section class="abs video-frame">
  <div class="video-still" role="img" aria-label="Video still of a calm lake at dusk">
    <div class="video-progress"><i></i></div>
    <div class="video-bar">
      <svg width="10" height="12"><rect x="0" y="0" width="3" height="12" fill="#fff"/><rect x="6" y="0" width="3" height="12" fill="#fff"/></svg>
      <svg width="12" height="12"><path d="M0 0l8 6-8 6z" fill="#fff"/><rect x="9" y="0" width="2" height="12" fill="#fff"/></svg>
      <span>0:33 / 3:25</span>
    </div>
  </div>
</section>

<section class="abs welcome">
  <div class="kicker">Welcome to</div>
  <h1>Dr. <b>Marla J. Kalvoric</b></h1>
  <p>I'm so glad you are here. Choosing to see a professional for issues in your life can be difficult but also possibly life changing. Many postpone seeking help because they believe doing so acknowledges failure on their part. Really? We seek the help of experts all the time (contractors, mechanics, chefs, etc...) and what is more important than your life? Consulting with a neutral party to act in your best interest can be time well spent. So if you are willing to take the time to invest in counseling, make sure that it is with someone that is worth your time.</p>
  <p>Choose a licensed psychologist with a doctoral degree (Ph.D. or PsyD.) - both have over 10 years of education in the field of psychology, extensive internships and comprehensive licensing exams. Others have far less education if any. Also, consider the therapist's approach to therapy. I use a straightforward approach (psychobabble available upon request) with brief, solution-oriented sessions.</p>
  <p>Experience also separates good psychologists from others with fewer and more proficient sessions. My 20+ years of professional experience and my life experience contributes to the empathetic perspective I use to relate to each person I see. I also believe it is the reason 90% of my practice is referral based and why many other psychologists in the area seek my services.</p>
  <p><b>DO NOT COMPROMISE.</b> Find an educated, licensed, experienced professional that you can relate to. Think about what it took to get you here and the importance resolving this issue can have on your life.</p>
</section>

<aside class="abs inquiry">
  <div class="inquiry-head">
    <div class="over">CONTACT US TODAY FOR YOUR</div>
    <div class="pill">QUICK INQUIRY</div>
    <div class="note">Fill out the form below and we'll be in touch<br>within 24 hours!</div>
  </div>
  <div class="inquiry-form">
    <div class="field">Name</div>
    <div class="field">Email</div>
    <div class="field">Phone</div>
    <div class="field tall">How Can we help you?</div>
    <div class="submit">SUBMIT</div>
  </div>
</aside>

<h2 class="abs section-title" style="top:1620px">Reviews From Patients</h2>
<div class="abs title-rule"></div>
<section class="abs reviews">
  <article class="review">
    <div class="avatar" role="img" aria-label="Patient photo"></div>
    <p>Lorem ipsum dolor sit amet, consectetur adipiscing elit, sed do eiusmod tempor incididunt ut labore et dolore magna aliqua. Ut enim ad minim veniam, quis nostrud exercitation ullamco laboris nisi ut aliquip ex ea commodo consequat. Duis aute irure dolor in reprehenderit in voluptate velit esse cillum dolore eu fugiat nulla pariatur. Excepteur sint occaecat cupidatat non proident, sunt in culpa qui officia deserunt mollit anim id est laborum.</p>
    <div class="who">Sam Ortell</div><div class="role">Lorem ipsum dolor</div>
  </article>
  <article class="review">
    <div class="avatar" role="img" aria-label="Patient photo"></div>
    <p>Lorem ipsum dolor sit amet, consectetur adipiscing elit, sed do eiusmod tempor incididunt ut labore et dolore magna aliqua. Ut enim ad minim veniam, quis nostrud exercitation ullamco laboris nisi ut aliquip ex ea commodo consequat. Duis aute irure dolor in reprehenderit in voluptate velit esse cillum dolore eu fugiat nulla pariatur. Excepteur sint occaecat cupidatat non proident, sunt in culpa qui officia deserunt mollit anim id est laborum.</p>
    <div class="who">Sam Ortell</div><div class="role">Lorem ipsum dolor</div>
  </article>
  <article class="review">
    <div class="avatar" role="img" aria-label="Patient photo"></div>
    <p>Lorem ipsum dolor sit amet, consectetur adipiscing elit, sed do eiusmod tempor incididunt ut labore et dolore magna aliqua. Ut enim ad minim veniam, quis nostrud exercitation ullamco laboris nisi ut aliquip ex ea commodo consequat. Duis aute irure dolor in reprehenderit in voluptate velit esse cillum dolore eu fugiat nulla pariatur. Excepteur sint occaecat cupidatat non proident, sunt in culpa qui officia deserunt mollit anim id est laborum.</p>
    <div class="who">Sam Ortell</div><div class="role">Lorem ipsum dolor</div>
  </article>
</section>

<h2 class="abs section-title" style="top:2136px;font-size:21px">A portion of all revenue is donated to</h2>
<div class="abs partners">
  <div class="partner" role="img" aria-label="Partner charity badge"><div class="partner-mark one"></div></div>
  <div class="partner" role="img" aria-label="Partner charity badge"><div class="partner-mark two"></div></div>
</div>

<svg class="abs footer-wave" viewBox="0 0 1200 90" preserveAspectRatio="none">
  <path d="M0 40 C 300 -10, 700 70, 1200 20 L1200 90 L0 90Z" fill="#fff"/>
  <path d="M0 55 C 300 5, 700 85, 1200 35 L1200 90 L0 90Z" fill="#1f5a82"/>
</svg>
<footer class="abs footer">
  <div class="foot-col" style="left:56px;width:262px">
    <h4>CLINICAL PSYCHOLOGIST</h4>
    <div class="sub">California # PSY20481</div>
    <div>Doctoral Degree in Clinical Psychology<br>Masters Degree in Counseling<br>Psychology Doctoral Internship, BCU<br>Medical Center Masters Internship,<br>Westbrook Clinic</div>
  </div>
  <div class="foot-col" style="left:328px;width:250px">
    <h4>CONTACT INFORMATION</h4>
    <div class="contact-line" style="margin-top:22px"><svg width="16" height="22" viewBox="0 0 16 22"><path d="M8 0a8 8 0 0 0-8 8c0 6 8 14 8 14s8-8 8-14a8 8 0 0 0-8-8zm0 11a3 3 0 1 1 0-6 3 3 0 0 1 0 6z" fill="#fff"/></svg><div style="line-height:20px">740 Harbor Lane, Suite 210<br>Bayview, CA 90000</div></div>
    <div class="contact-line"><svg width="18" height="18" viewBox="0 0 24 24"><path d="M6.6 10.8a15 15 0 0 0 6.6 6.6l2.2-2.2a1 1 0 0 1 1-.25 11.4 11.4 0 0 0 3.6.57 1 1 0 0 1 1 1V20a1 1 0 0 1-1 1A17 17 0 0 1 3 4a1 1 0 0 1 1-1h3.5a1 1 0 0 1 1 1c0 1.25.2 2.45.57 3.57a1 1 0 0 1-.25 1z" fill="#fff"/></svg><span style="font-size:17px">(555) 318 4402</span></div>
    <div class="contact-line"><svg width="20" height="15" viewBox="0 0 24 18"><rect x="0" y="0" width="24" height="18" fill="#fff"/><path d="M0 0l12 10 12-10" fill="none" stroke="#1f5a82" stroke-width="2"/></svg><span>mk@drkalvoric.com</span></div>
  </div>
  <div class="foot-col" style="left:595px">
    <h4>FIND US ON MAP</h4>
    <div class="map-tile" role="img" aria-label="Street map showing the office location"></div>
  </div>
  <div class="foot-col" style="left:866px">
    <h4>QUICK LINKS</h4>
    <div style="margin-top:14px">Home<br>Sessions<br>Resources<br>Bio<br>Contact</div>
  </div>
</footer>

<div class="abs bottom-bar">
  <div class="copyright">©2016 Dr. Marla J. Kalvoric. All Rights Reserved.</div>
  <div class="socials"><span><i></i>Rivo</span><span><i></i>Friendora</span><span><i></i>Chirpline</span></div>
</div>

</body>
</html>
```